Business card design for new eCommerce site focusing on integrity and strong businsess tactics

We need a business card that will stand out and be memorable. Something with color that matches our company logo colors. Think high end version of Pactivo. There are 2 logos provided. The parent company is called Amber Ledge Partners and we are presenting a new and very exciting eCommerce site called BrightHarborTrade.example.

Target Market(s)

Our target markets are in the Activities, Food and Beverage, Health and Beauty

Industry/Entity Type

Marketing

Contact Information for Business Card

We have 4 members that need cards...I will provide all info to the winner of the design contest
Business Address is
4870 West 63rd Avenue, Suite C207
Phoenix AZ 85731

Font styles to use
Serif
Sans Serif

Colors

Designer to choose colors to be used in the design.

Requirements
Must have
• The card must be memorable...should be unique in design but must exude integrity and be playful .
• I have provided several colors or our parent company...please feel free to use which ever
Nice to have
• I will leave this up to you. Feel free to use other images of your choosing that wraps around our client.....Activities, Dining, Health, Beauty
Should not have
• just dont be boring

```html
<!DOCTYPE html>
<html lang="en">
<head>
<meta charset="utf-8">
<title>Amber Ledge Partners – Business Card</title>
<link rel="stylesheet" href="https://fonts.googleapis.com/css2?family=Roboto:wght@400;500;700&display=swap">
<style>
  :root {
    --lime: #9dc33b;
    --lime-soft: #8fbf4a;
    --teal: #1f7b7d;
    --teal-mid: #3d9a86;
    --brand-teal: #2c8a89;
    --paper: #f4f4f2;
    --backdrop: #bdbdbd;
    --white: #ffffff;
  }
  * { margin: 0; padding: 0; box-sizing: border-box; }
  html, body { width: 1200px; height: 576px; overflow: hidden; }
  body {
    background: var(--backdrop);
    font-family: "Roboto", sans-serif;
    position: relative;
  }
  .card {
    position: absolute;
    top: 138px;
    width: 484px;
    height: 294px;
    border-radius: 14px;
    overflow: hidden;
  }
  /* Front */
  .card-front {
    left: 82px;
    background: linear-gradient(180deg, var(--lime) 0%, var(--lime-soft) 30%, var(--teal-mid) 62%, var(--teal) 100%);
  }
  .front-mark {
    position: absolute;
    left: 181px; top: 61px;
    width: 122px; height: 122px;
    border-radius: 50%;
    background: var(--white);
  }
  .front-name {
    position: absolute;
    left: 0; right: 0; top: 192px;
    text-align: center;
    color: var(--white);
    font-weight: 500;
    line-height: 1;
  }
  .front-name .name-main { display: block; font-size: 28px; }
  .front-name .name-sub { display: block; font-size: 12px; letter-spacing: 4px; margin-top: 3px; }

  /* Back */
  .card-back {
    left: 602px;
    width: 481px;
    height: 292px;
    background: var(--paper);
  }
  .back-shape { position: absolute; inset: 0; }
  .holder {
    position: absolute;
    left: 22px; top: 31px;
    color: var(--white);
  }
  .holder-name { font-size: 19px; font-weight: 700; }
  .holder-title { font-size: 11px; margin-top: 6px; }
  .contact {
    position: absolute;
    left: 22px; top: 174px;
    color: var(--white);
    font-size: 12.5px;
    list-style: none;
  }
  .contact li { display: flex; align-items: center; gap: 10px; height: 18px; }
  .contact svg { width: 11px; height: 11px; fill: var(--white); }
  .address {
    position: absolute;
    left: 22px; top: 233px;
    color: var(--white);
    font-size: 12.5px;
    line-height: 17px;
    font-style: normal;
  }
  .back-mark {
    position: absolute;
    left: 316px; top: 70px;
    width: 106px; height: 106px;
    border-radius: 50%;
    background: var(--brand-teal);
  }
  .back-name {
    position: absolute;
    left: 274px; width: 190px; top: 186px;
    text-align: center;
    color: var(--brand-teal);
    font-weight: 500;
    line-height: 1;
  }
  .back-name .name-main { display: block; font-size: 24px; }
  .back-name .name-sub { display: block; font-size: 11px; letter-spacing: 3.5px; margin-top: 3px; }
</style>
</head>
<body>

<section class="card card-front" aria-label="Card front">
  <div class="front-mark"></div>
  <div class="front-name">
    <span class="name-main">Amber Ledge</span>
    <span class="name-sub">partners</span>
  </div>
</section>

<section class="card card-back" aria-label="Card back">
  <svg class="back-shape" viewBox="0 0 481 292" preserveAspectRatio="none">
    <defs>
      <linearGradient id="backGradient" x1="0" y1="0" x2="0" y2="1">
        <stop offset="0" stop-color="#9dc33b"/>
        <stop offset="0.35" stop-color="#8fbf4a"/>
        <stop offset="0.65" stop-color="#3d9a86"/>
        <stop offset="1" stop-color="#2a8580"/>
      </linearGradient>
    </defs>
    <path d="M0 0 H298 C250 60 225 130 240 200 C250 245 270 275 290 292 H0 Z" fill="url(#backGradient)"/>
    <path d="M318 0 C285 35 255 90 244 150 L236 150 C246 90 275 35 306 0 Z" fill="#9dc33b"/>
  </svg>

  <div class="holder">
    <p class="holder-name">Employee Name</p>
    <p class="holder-title">Managing Director</p>
  </div>

  <ul class="contact">
    <li>
      <svg viewBox="0 0 12 12"><path d="M1 3.5C1 2 2 1 3 1h6c1 0 2 1 2 2.5L9 4.5 8 3H4L3 4.5Z M3 5.5h6l1 5H2Z"/></svg>
      1800-555-0142
    </li>
    <li>
      <svg viewBox="0 0 12 12"><path d="M1 2.5h10v7H1Z M1.8 3.2 6 6.5 10.2 3.2" fill="none" stroke="#fff" stroke-width="1.2"/></svg>
      name@brightharbortrade.example
    </li>
    <li>
      <svg viewBox="0 0 12 12"><g fill="none" stroke="#fff" stroke-width="1"><circle cx="6" cy="6" r="5"/><ellipse cx="6" cy="6" rx="2.2" ry="5"/><path d="M1 6h10"/></g></svg>
      www.brightharbortrade.example
    </li>
  </ul>

  <address class="address">
    4870 West 63rd Avenue, Suite<br>
    C207, Phoenix AZ 85731
  </address>

  <div class="back-mark"></div>
  <div class="back-name">
    <span class="name-main">Amber Ledge</span>
    <span class="name-sub">partners</span>
  </div>
</section>

</body>
</html>
```